Hello my Name is Elias Moreno. I buy and sell vintage comic books, you can refer to my instragram page qpkz.comics to get ideas and inspiration. For the front of the card I would like my company logo QPKZ Comics with a yellow and black background with the bat signal or bat emblem like on my IG page and with my info Elias Moreno as the Owner and address/ phone number, PO Box 617283, Miami, FL 33827, 305-482-6170 and that I buy and sell comics & collectables . Also feel free to be open to other ideas if you want. Im not stuck on one design. For the back of the card I would like for it to say follow me on Instagram QPKZ.Comics with the ig emblem. Also would like the card to be vertical if possible. Thanks

```html
<!DOCTYPE html>
<html lang="en">
<head>
<meta charset="utf-8">
<title>QPKZ Comics — Business Card</title>
<link rel="stylesheet" href="https://fonts.googleapis.com/css2?family=Source+Sans+3:wght@400;700&display=swap">
<style>
  :root {
    --page-bg: #d8d5d2;
    --card-yellow: #fcc515;
    --card-pale: #eeebe9;
    --ink: #111111;
    --emblem-black: #0b0b0b;
    --emblem-text: #ffffff;
  }
  * { margin: 0; padding: 0; box-sizing: border-box; }
  html, body {
    width: 1200px;
    height: 900px;
    overflow: hidden;
    background: var(--page-bg);
    font-family: "Source Sans 3", Arial, sans-serif;
  }
  .business-card {
    position: absolute;
    left: 180px;
    top: 190px;
    width: 839px;
    height: 520px;
    background: var(--card-pale);
    overflow: hidden;
    box-shadow: 0 10px 30px rgba(0,0,0,0.18);
  }
  .card-yellow-panel {
    position: absolute;
    left: 0; top: 0;
    width: 600px;
    height: 100%;
    background: var(--card-yellow);
  }
  .contact-block {
    position: absolute;
    left: 40px;
    top: 0;
    color: var(--ink);
  }
  .owner-name {
    position: absolute;
    top: 76px;
    white-space: nowrap;
    font-size: 30px;
    font-weight: 700;
    letter-spacing: 0.3px;
    line-height: 1;
  }
  .owner-title {
    position: absolute;
    top: 110px;
    font-size: 26px;
    font-weight: 400;
    line-height: 1;
  }
  .contact-phone {
    position: absolute;
    top: 189px;
    display: flex;
    align-items: center;
    gap: 10px;
    white-space: nowrap;
    font-size: 25px;
    line-height: 1;
  }
  .contact-phone svg { width: 18px; height: 18px; }
  .contact-address {
    position: absolute;
    top: 250px;
    white-space: nowrap;
    font-size: 23px;
    line-height: 32px;
  }
  .social-follow {
    position: absolute;
    top: 344px;
    white-space: nowrap;
    font-size: 23px;
    line-height: 32px;
  }
  .social-handle {
    display: flex;
    align-items: center;
    gap: 10px;
  }
  .social-marker {
    width: 22px;
    height: 22px;
    background: var(--ink);
  }
  .tagline {
    position: absolute;
    top: 459px;
    white-space: nowrap;
    font-size: 22px;
    line-height: 1;
  }
  .brand-emblem {
    position: absolute;
    left: 410px;
    top: 52px;
    width: 380px;
    height: 380px;
    border-radius: 50%;
    background: var(--emblem-black);
    display: flex;
    align-items: center;
    justify-content: center;
  }
  .brand-name {
    color: var(--emblem-text);
    font-size: 60px;
    font-weight: 700;
    line-height: 1;
    white-space: nowrap;
  }
</style>
</head>
<body>
  <div class="business-card">
    <div class="card-yellow-panel"></div>

    <div class="contact-block">
      <p class="owner-name">ELIAS MORENO</p>
      <p class="owner-title">OWNER</p>

      <p class="contact-phone">
        <svg viewBox="0 0 24 24" aria-hidden="true">
          <path fill="#111" d="M3 9c0-3 4-5 9-5s9 2 9 5v2h-5V9c-1-.6-2.4-1-4-1s-3 .4-4 1v2H3z"/>
          <path fill="#111" d="M7 12h10l3 8H4z"/>
          <circle cx="12" cy="16" r="2" fill="#fcc515"/>
        </svg>
        305-482-6170
      </p>

      <p class="contact-address">PO Box 617283,<br>Miami, FL 33827</p>

      <div class="social-follow">
        <p>Follow me on</p>
        <p class="social-handle"><span class="social-marker"></span>QPKZ.COMICS</p>
      </div>

      <p class="tagline">WE BUY AND SELL COMICS &amp; COLLECTABLES</p>
    </div>

    <div class="brand-emblem">
      <span class="brand-name">QPKZ Comics</span>
    </div>
  </div>
</body>
</html>
```